Hollis Varner Building Company, Inc.
Business Cards, Letterhead, Envelopes, Fax Cover
Professional
Dean K. Molloy
PO Box 48217
Raleigh, NC 27915
dean@hollisvarnerco.example
www.hollisvarnerco.example
looking for a traditional style card, however nothing dated. same goes for the stationary. Something that is creative , but still shows professionalism and adaptable to the corporate environment. We don't want gloss cards. waiting on office and fax #'s. should have those in a day or two. As for the font, I put use same as logo font, but may want to see standard as well.
HV

```html
<!DOCTYPE html>
<html lang="en">
<head>
<meta charset="utf-8">
<title>Hollis Varner Building Company, Inc. — Business Cards</title>
<link rel="stylesheet" href="https://fonts.googleapis.com/css2?family=Arimo:wght@400;700&display=swap">
<style>
  :root {
    --navy: #22386b;
    --navy-deep: #1c2f5c;
    --ink: #3a3f48;
    --muted: #6b707a;
    --rule: #b9bcc2;
    --stripe: #9aa0a8;
    --card-light: #fbfbfc;
    --card-shade: #e4e5e8;
    --stage: #ebe8e3;
    --white: #ffffff;
  }
  * { box-sizing: border-box; margin: 0; padding: 0; }
  html, body { width: 1200px; height: 714px; overflow: hidden; }
  body {
    background: var(--stage);
    font-family: "Arimo", Arial, sans-serif;
    position: relative;
  }
  .card {
    position: absolute;
    border-radius: 14px;
    overflow: hidden;
    box-shadow: 0 4px 10px rgba(0,0,0,0.12);
  }
  .card--light { background: linear-gradient(160deg, var(--card-light) 40%, var(--card-shade) 100%); }
  .card--navy { background: var(--navy); }

  /* front card */
  .card-front { left: 86px; top: 120px; width: 471px; height: 271px; z-index: 2; }
  .brand-block {
    position: absolute; left: 14px; top: 70px; width: 250px;
    text-align: center; color: var(--navy);
    font-weight: 400; text-transform: uppercase;
  }
  .brand-mark {
    width: 44px; height: 44px; background: var(--navy);
    margin: 0 auto 14px;
  }
  .brand-name { font-size: 22px; letter-spacing: 1px; line-height: 1.1; }
  .brand-sub { font-size: 13px; letter-spacing: 4px; margin-top: 3px; }
  .divider {
    position: absolute; left: 272px; top: 48px; width: 1px; height: 158px;
    background: var(--rule);
  }
  .contact { position: absolute; left: 286px; top: 52px; color: var(--ink); font-size: 10px; line-height: 1.5; }
  .contact-name { font-size: 19px; font-weight: 700; color: var(--navy); line-height: 1.1; }
  .contact-title { font-size: 11px; color: var(--muted); margin-bottom: 14px; }
  .contact-address { margin-bottom: 14px; }
  .front-band { position: absolute; left: 0; bottom: 0; width: 100%; height: 50px; }
  .front-url {
    position: absolute; right: 24px; bottom: 10px;
    color: var(--white); font-size: 11px; font-weight: 700; letter-spacing: 0.2px;
    white-space: nowrap;
  }

  /* back cards */
  .card-back-navy { left: 595px; top: 65px; width: 466px; height: 271px; }
  .card-back-light { left: 353px; top: 360px; width: 466px; height: 274px; z-index: 1; }
  .back-content {
    position: absolute; inset: 0;
    display: flex; flex-direction: column; align-items: center; justify-content: center;
    padding-top: 10px;
  }
  .back-name {
    font-size: 26px; font-weight: 400; text-transform: uppercase; letter-spacing: 1px;
  }
  .back-url { font-size: 13px; font-weight: 700; margin-top: 18px; }
  .card-back-navy .back-name, .card-back-navy .back-url { color: var(--white); }
  .card-back-light .back-name, .card-back-light .back-url { color: var(--navy); }
</style>
</head>
<body>

  <section class="card card--navy card-back-navy" aria-label="Business card back, navy">
    <div class="back-content">
      <div class="back-name">Hollis Varner</div>
      <div class="back-url">www.hollisvarnerco.example</div>
    </div>
  </section>

  <section class="card card--light card-back-light" aria-label="Business card back, white">
    <div class="back-content">
      <div class="back-name">Hollis Varner</div>
      <div class="back-url">www.hollisvarnerco.example</div>
    </div>
  </section>

  <section class="card card--light card-front" aria-label="Business card front">
    <div class="brand-block">
      <div class="brand-mark"></div>
      <div class="brand-name">Hollis Varner</div>
      <div class="brand-sub">Building Company</div>
    </div>

    <div class="divider"></div>

    <div class="contact">
      <div class="contact-name">Dean K. Molloy</div>
      <div class="contact-title">Principal</div>
      <div class="contact-address">PO Box 48217<br>Raleigh, NC 27915</div>
      <div class="contact-lines">
        Phone: 123-456-7890<br>
        Cell: 919-555-0142<br>
        Fax: 123-456-7890<br>
        Email: dean@hollisvarnerco.example
      </div>
    </div>

    <svg class="front-band" viewBox="0 0 471 50" preserveAspectRatio="none" aria-hidden="true">
      <rect x="0" y="14" width="471" height="5" fill="var(--stripe)"/>
      <rect x="0" y="22" width="471" height="3" fill="var(--rule)"/>
      <path d="M250 12 H471 V50 H272 Q262 50 260 40 Z" fill="var(--navy-deep)"/>
    </svg>
    <div class="front-url">www.hollisvarnerco.example</div>
  </section>

</body>
</html>
```